Letter and Envelope Design For Harborline Realty

Please design a letter and an envelope incorporating our logo (See Attached). We are also launched a business card contest. Since we want them to match, please feel free to submit a design for both the business card and also the letter design and envelope.

Requirements
Must have
• The envelope, the letter and the business cards must match somehow connecting the designs. We want them to have something that holds them together besides the logo.

```html
<!DOCTYPE html>
<html lang="en">
<head>
<meta charset="utf-8">
<title>Harborline Realty – Letterhead and Envelope</title>
<link href="https://fonts.googleapis.com/css2?family=Montserrat:wght@500&family=Open+Sans:wght@400;700&family=Arimo:wght@700&display=swap" rel="stylesheet">
<style>
  :root {
    --brand-blue: #00188a;
    --paper: #fbfbfb;
    --backdrop: #e4e4e4;
    --ink: #3a3a3a;
    --ink-strong: #111;
    --white: #ffffff;
    --watermark: #eceef4;
  }
  * { margin: 0; padding: 0; box-sizing: border-box; }
  html, body { width: 1200px; height: 825px; overflow: hidden; }
  body {
    background: var(--backdrop);
    font-family: "Open Sans", Arial, sans-serif;
    position: relative;
  }
  .sheet { position: absolute; background: var(--paper); overflow: hidden; }
  .letter { left: 80px; top: 84px; width: 465px; height: 656px; }
  .envelope-back { left: 585px; top: 259px; width: 534px; height: 231px; }
  .envelope-front { left: 585px; top: 509px; width: 534px; height: 231px; }

  .brand-band {
    position: absolute; left: 0; right: 0; height: 39px;
    background: var(--brand-blue); color: var(--white);
  }
  .letter .brand-band { top: 15px; --name-x: 83px; --address-x: 254px; --divider-x: 345px; --list-x: 351px; }
  .envelope-front .brand-band { top: 17px; --name-x: 84px; --address-x: 321px; --divider-x: 413px; --list-x: 419px; }

  .brand-mark {
    position: absolute; left: 34px; top: 0; width: 39px; height: 39px;
    border-radius: 50%; border: 3px solid var(--white);
  }
  .brand-name {
    position: absolute; left: var(--name-x); top: 13px;
    font-family: "Montserrat", sans-serif; font-weight: 500;
    font-size: 10.5px; line-height: 13px; letter-spacing: 1.2px; white-space: nowrap;
  }
  .contact-address, .contact-list {
    position: absolute; top: 6px; font-size: 5.6px; line-height: 9px; white-space: nowrap;
  }
  .contact-address { left: var(--address-x); font-style: normal; }
  .contact-address strong { font-weight: 700; }
  .contact-divider {
    position: absolute; left: var(--divider-x); top: 8px; width: 1px; height: 23px; background: var(--white);
  }
  .contact-list { left: var(--list-x); list-style: none; top: 7px; }
  .contact-list li { display: flex; align-items: center; gap: 3px; height: 9px; }
  .contact-list svg { width: 5px; height: 5px; fill: var(--white); flex: none; }

  .watermark-ring {
    position: absolute; left: 88px; top: 204px; width: 288px; height: 288px;
    border: 11px solid var(--watermark); border-radius: 50%;
  }
  .salutation {
    position: absolute; left: 30px; top: 135px;
    font-family: "Arimo", Arial, sans-serif; font-weight: 700;
    font-size: 10.5px; color: var(--ink-strong);
  }
  .letter-body { position: absolute; left: 30px; top: 163px; width: 406px; color: var(--ink); }
  .letter-body p {
    font-size: 8.6px; line-height: 12.2px; text-align: justify;
    letter-spacing: -0.12px; margin-bottom: 12.2px;
  }
  .signature-area {
    position: absolute; left: 30px; top: 482px; width: 72px; height: 34px;
    background: linear-gradient(90deg, #efefef, #f6f6f6); border-radius: 3px;
  }
  .envelope-flap { position: absolute; left: 1px; top: 0; width: 534px; height: 65px; }
</style>
</head>
<body>

<section class="sheet letter">
  <header class="brand-band">
    <span class="brand-mark"></span>
    <span class="brand-name">HARBORLINE REALTY</span>
    <address class="contact-address">
      <strong>Harborline Realty</strong><br>Po. box 201, Street Name,<br>City Name, Zip Code - 00000
    </address>
    <span class="contact-divider"></span>
    <ul class="contact-list">
      <li><svg viewBox="0 0 10 10"><path d="M2 1h2l1 2-1.3 1a6 6 0 0 0 2.3 2.3L7 5l2 1v2a1 1 0 0 1-1 1A7 7 0 0 1 1 2a1 1 0 0 1 1-1z"/></svg>555-014-2290</li>
      <li><svg viewBox="0 0 10 10"><path d="M1 2h8v6H1zM1.5 2.5 5 5.5l3.5-3" stroke="#00188a" stroke-width="0.8"/></svg>info@harborlinerealty.com</li>
      <li><svg viewBox="0 0 10 10"><circle cx="5" cy="5" r="4"/></svg>info@harborlinerealty.com</li>
    </ul>
  </header>

  <div class="watermark-ring"></div>

  <p class="salutation">Dlear Mr. John,</p>
  <article class="letter-body">
    <p>Lorem Ipsum is simply dummy text of the printing and typesetting industry. Lorem Ipsum has been the industry's standard dummy text ever since the 1500s, when an unknown printer took a galley of type and scrambled it to make a type specimen book. It has survived not only five centuries, but also the leap into electronic typesetting, remaining essentially unchanged.</p>
    <p>The standard chunk of Lorem Ipsum used since the 1500s is reproduced below for those interested. Sections 1.10.32 and 1.10.33 from "de Finibus Bonorum et Malorum" by Cicero are also reproduced in their exact original form, accompanied by English versions from the 1914 translation by H. Rackham</p>
    <p>Lorem Ipsum is simply dummy text of the printing and typesetting industry. Lorem Ipsum has been the industry's standard dummy text ever since the 1500s, when an unknown printer took a galley of type and scrambled it to make a type specimen book. It has survived not only five centuries, but also the leap into electronic typesetting, remaining essentially unchanged. It was popularised in the</p>
    <p>The standard chunk of Lorem Ipsum used since the 1500s is reproduced below for those interested. Sections 1.10.32 and 1.10.33 from "de Finibus Bonorum et Malorum" by Cicero are also reproduced in their exact original form, accompanied by English versions from the 1914 translation by H. Rackham</p>
    <p>The standard chunk of Lorem Ipsum used since the 1500s is reproduced below for those interested. Sections 1.10.32 and 1.10.33 from "de Finibus Bonorum et Malorum" by Cicero are also reproduced in their exact original form.</p>
  </article>

  <div class="signature-area" role="img" aria-label="Handwritten signature of the sender"></div>
</section>

<section class="sheet envelope-back">
  <svg class="envelope-flap" viewBox="0 0 534 65" preserveAspectRatio="none" aria-hidden="true">
    <path d="M0 0H533L526 50Q523 64 508 64H25Q10 64 7 50Z" fill="#00188a"/>
  </svg>
</section>

<section class="sheet envelope-front">
  <header class="brand-band">
    <span class="brand-mark"></span>
    <span class="brand-name">HARBORLINE REALTY</span>
    <address class="contact-address">
      <strong>Harborline Realty</strong><br>Po. box 201, Street Name,<br>City Name, Zip Code - 00000
    </address>
    <span class="contact-divider"></span>
    <ul class="contact-list">
      <li><svg viewBox="0 0 10 10"><path d="M2 1h2l1 2-1.3 1a6 6 0 0 0 2.3 2.3L7 5l2 1v2a1 1 0 0 1-1 1A7 7 0 0 1 1 2a1 1 0 0 1 1-1z"/></svg>555-014-2290</li>
      <li><svg viewBox="0 0 10 10"><path d="M1 2h8v6H1zM1.5 2.5 5 5.5l3.5-3" stroke="#00188a" stroke-width="0.8"/></svg>info@harborlinerealty.com</li>
      <li><svg viewBox="0 0 10 10"><circle cx="5" cy="5" r="4"/></svg>info@harborlinerealty.com</li>
    </ul>
  </header>
</section>

</body>
</html>
```